Business card

We need a business card design for our company based in Auckland , New Zealand called 'Ridge Studio Limited'. We provide architectural services. We would like to see designs that use the max. three colours (such as white, black, grey) The final design should communicate financial safety and growth."
Also I will provide our company logo. I would like to the logo to be embeded onto our business card.

Target Market(s)

new residential house, alteration & addition & light commericila design & drafting service

Industry/Entity Type

Architecture

Contact Information for Business Card

Company name: Ridge Studio Limited
Name: Mark Delford
Job title: architectural designer & Design LBP
email address: mark@ridgestudio.co.nz
mobile number: 02 5163 2290
web site: www.ridgestudio.co.nz

Requirements
Must have
• My project must have..
• - embeded logo (attached company logo)
• I don't have a bigger version for our company logo, but I have one old one, so you can remove the word from it)
• - insert the attached small BKTW logo & LBP logo
• - creative, simple and clear business card.
• - Max. three colours
Nice to have
• - Here are the samples I would like to share with you: http://www.plimvora.com/blog/minimalistic-business-card-designs/
• I would like to have my business card like one of the creation.
Should not have
• TBA

```html
<!DOCTYPE html>
<html lang="en">
<head>
<meta charset="utf-8">
<title>Ridge Studio Limited — Business Card</title>
<link rel="stylesheet" href="https://fonts.googleapis.com/css2?family=Source+Sans+3:wght@400;600;700&display=swap">
<style>
  :root {
    --board: #e3e3e3;
    --board-glow: #e9e9e9;
    --card: #ffffff;
    --accent: #b3001b;
    --accent-soft: #f6e4e7;
    --ink: #1f1f1f;
    --badge: #2a2a2a;
    --shadow: rgba(0, 0, 0, 0.45);
  }
  * { box-sizing: border-box; margin: 0; padding: 0; }
  html, body { width: 1200px; height: 849px; overflow: hidden; }
  body {
    position: relative;
    background: radial-gradient(ellipse 420px 400px at 50% 52%, var(--board-glow), var(--board));
    font-family: "Source Sans 3", "Myriad Pro", sans-serif;
    color: var(--ink);
  }

  /* brand lockup: plain circle + name in ink */
  .brand-lockup {
    position: absolute;
    display: flex;
    align-items: center;
    transform: translate(-50%, -50%);
    white-space: nowrap;
  }
  .brand-dot { border-radius: 50%; background: var(--accent); flex: none; }
  .brand-name { color: var(--ink); font-weight: 600; letter-spacing: 0.04em; }

  .brand-lockup--hero { left: 583px; top: 234px; gap: 20px; }
  .brand-lockup--hero .brand-dot { width: 90px; height: 90px; }
  .brand-lockup--hero .brand-name { font-size: 32px; }

  /* cards */
  .card {
    position: absolute;
    top: 392px;
    width: 345px;
    height: 221px;
    background: var(--card);
    border-radius: 28px;
    box-shadow: 6px 8px 10px var(--shadow);
    overflow: hidden;
  }
  .card--front { left: 204px; }
  .card--back { left: 617px; }

  .card--front .brand-lockup { left: 50%; top: 50%; gap: 12px; }
  .card--front .brand-dot { width: 48px; height: 48px; }
  .card--front .brand-name { font-size: 19px; }

  .back-watermark {
    position: absolute;
    left: 2px;
    top: 40px;
    width: 156px;
    height: 156px;
    border-radius: 50%;
    border: 14px solid var(--accent-soft);
  }
  .back-mark {
    position: absolute;
    left: 154px;
    top: 36px;
    width: 34px;
    height: 34px;
    border-radius: 50%;
    background: var(--accent);
  }
  .contact {
    position: absolute;
    left: 0;
    right: 0;
    top: 90px;
    text-align: center;
    line-height: 1;
  }
  .contact__company {
    color: var(--ink);
    font-weight: 700;
    font-size: 15px;
    letter-spacing: 0.03em;
    margin-left: 6px;
  }
  .contact__title { font-size: 8px; font-weight: 700; margin-top: 6px; }
  .contact__name { font-size: 13px; font-weight: 400; margin-top: 8px; }
  .contact__details { font-size: 11.5px; font-weight: 600; margin-top: 6px; line-height: 14.5px; }

  .badge {
    position: absolute;
    right: 14px;
    bottom: 14px;
    width: 28px;
    height: 28px;
    border-radius: 50%;
    background: var(--badge);
    box-shadow: 0 0 0 2px var(--card), 0 0 0 3px #999;
  }
</style>
</head>
<body>
  <div class="brand-lockup brand-lockup--hero">
    <span class="brand-dot"></span>
    <span class="brand-name">Ridge Studio Limited</span>
  </div>

  <section class="card card--front" aria-label="Card front">
    <div class="brand-lockup">
      <span class="brand-dot"></span>
      <span class="brand-name">Ridge Studio</span>
    </div>
  </section>

  <section class="card card--back" aria-label="Card back">
    <div class="back-watermark"></div>
    <div class="back-mark"></div>
    <div class="contact">
      <p class="contact__company">Ridge Studio Limited</p>
      <p class="contact__title">architectural designer &amp; Design LBP</p>
      <p class="contact__name">Mark Delford</p>
      <p class="contact__details">mark@ridgestudio.co.nz<br>02 5163 2290<br>www.ridgestudio.co.nz</p>
    </div>
    <div class="badge" role="img" aria-label="Professional membership badge"></div>
  </section>
</body>
</html>
```